Webshop for furniture and lamps

We need a design for a web shop with APP that should have two options:
1-Webshop in general which should attract to private customer in general and
2-Website that is meant to attract big customers as hotels and restaurants who would have their own customerize login.

That's the idea behind the shop.

It should be diveded into 4 parts
vintage furniture
rattan set outdoor and indoor
lamps and
wooden wall decor

The name of the shop is loma vereda!

Please kindly make me an offer.

Reason: Dear designers, so far there hasn't been a design that really matched. Look up German web sites like www.glimmerhof-wohnen.de or www.sitzraum77.de... Haven't been convinced by designs! Sorry folks. Please submit some new ones. Kind regards Ned

```html
<!DOCTYPE html>
<html lang="en">
<head>
<meta charset="utf-8">
<title>Welcome Visitors</title>
<link rel="stylesheet" href="https://fonts.googleapis.com/css2?family=Open+Sans:wght@300;400;700&display=swap">
<style>
  :root {
    --text: #ffffff;
    --shade-deep: #1e1611;
    --shade-warm: #4a3628;
    --shade-mid: #6a5c52;
    --shade-light: #8a8480;
  }
  html, body {
    margin: 0;
    padding: 0;
    width: 1200px;
    height: 581px;
    overflow: hidden;
    background: var(--shade-deep);
  }
  .welcome {
    position: relative;
    width: 1200px;
    height: 581px;
    overflow: hidden;
    font-family: "Open Sans", sans-serif;
    color: var(--text);
    text-align: center;
  }
  .welcome__backdrop {
    position: absolute;
    inset: 0;
    background:
      radial-gradient(ellipse 520px 260px at 720px 380px, var(--shade-light) 0%, rgba(138,132,128,0) 100%),
      radial-gradient(ellipse 900px 420px at 600px 260px, var(--shade-warm) 0%, var(--shade-deep) 100%);
  }
  .welcome__title {
    position: absolute;
    top: 82px;
    left: 0;
    width: 100%;
    margin: 0;
    font-size: 54px;
    font-weight: 700;
    letter-spacing: 0.5px;
    line-height: 1.2;
  }
  .welcome__avatar {
    position: absolute;
    top: 193px;
    left: 552px;
    width: 96px;
    height: 96px;
  }
  .welcome__invite {
    position: absolute;
    top: 332px;
    left: 0;
    width: 100%;
    margin: 0;
    font-size: 21px;
    font-weight: 300;
    line-height: 34px;
  }
  .welcome__signin {
    position: absolute;
    top: 446px;
    left: 0;
    width: 100%;
    margin: 0;
    font-size: 21px;
    font-weight: 300;
    line-height: 34px;
  }
  .welcome strong {
    font-weight: 700;
  }
  .welcome__terms {
    position: absolute;
    top: 525px;
    left: 0;
    width: 100%;
    margin: 0;
    font-size: 16px;
    font-weight: 400;
  }
</style>
</head>
<body>
  <main class="welcome">
    <div class="welcome__backdrop" role="img" aria-label="Dimmed photo of a hotel bedroom with a wooden block wall, bed and bedside lamp"></div>

    <h1 class="welcome__title">WELCOME VISITORS</h1>

    <svg class="welcome__avatar" viewBox="0 0 96 96" aria-hidden="true">
      <circle cx="48" cy="48" r="48" fill="#ffffff"/>
      <circle cx="48" cy="34" r="14" fill="#4a3a30"/>
      <path d="M22 76 V64 Q22 52 34 52 H62 Q74 52 74 64 V76 Z" fill="#4a3a30"/>
      <path d="M40 52 L48 66 L56 52 Z" fill="#ffffff"/>
    </svg>

    <p class="welcome__invite">
      Join us and get our special promo every week<br>
      for New Member please <strong>SIGN UP</strong> here
    </p>

    <p class="welcome__signin">
      Business Membership <strong>SIGN IN</strong> here and Private Customer Membership <strong>SIGN IN</strong> here
    </p>

    <p class="welcome__terms">terms and conditions</p>
  </main>
</body>
</html>
```